Brellin Works
Professional
Dennis Falwick
CEO
5184-2 Calloway Rd #2267
Houston, TX 77091
Dennis@BrellinWorks.example
BrellinWorks.example
Feel free to play with the function of the business card if possible as seen in: http://www.kelvorastudio.example/blog/wp-content/uploads/2009/12/lock-picking-business-card.jpg. Card can be paper plastic or metal.
Our company specializes in artificial intelligence, Unmanned aerial vehicles human-machine interfaces and lasers. Please keep this in mind in your designs.
surprise me, I will refine my requirement here after I see a few submissions.
Here are the business logo files

```html
<!DOCTYPE html>
<html lang="en">
<head>
<meta charset="utf-8">
<title>Brellin Works – Business Card, Back Side</title>
<link href="https://fonts.googleapis.com/css2?family=Exo+2:wght@600&display=swap" rel="stylesheet">
<style>
  :root {
    --page-bg: #e6e7e8;
    --card-base: #474747;
    --card-band: #525252;
    --card-band-light: #5d5d5d;
    --card-edge: #3a3a3a;
    --brand-text: #ffffff;
    --brand-dot: #d9d4d0;
  }
  * { margin: 0; padding: 0; box-sizing: border-box; }
  html, body {
    width: 1200px;
    height: 895px;
    overflow: hidden;
    background: var(--page-bg);
  }
  .stage {
    position: relative;
    width: 1200px;
    height: 895px;
  }
  .card {
    position: absolute;
    left: 180px;
    top: 192px;
    width: 840px;
    height: 510px;
  }
  .card-shape {
    position: absolute;
    inset: 0;
    width: 840px;
    height: 510px;
    display: block;
  }
  .brand {
    position: absolute;
    left: 90px;
    top: 215px;
    display: flex;
    align-items: center;
    gap: 34px;
  }
  .brand-dot {
    width: 72px;
    height: 72px;
    border-radius: 50%;
    background: var(--brand-dot);
    flex: none;
  }
  .brand-name {
    font-family: "Exo 2", sans-serif;
    font-weight: 600;
    font-size: 64px;
    letter-spacing: 2px;
    text-transform: uppercase;
    color: var(--brand-text);
    line-height: 1;
    white-space: nowrap;
  }
</style>
</head>
<body>
  <main class="stage">
    <section class="card" aria-label="Brellin Works business card, back side">
      <svg class="card-shape" viewBox="0 0 840 510" xmlns="http://www.w3.org/2000/svg" aria-hidden="true">
        <defs>
          <clipPath id="card-outline">
            <polygon points="48,0 792,0 840,48 840,462 792,510 48,510 0,462 0,48"/>
          </clipPath>
        </defs>
        <g clip-path="url(#card-outline)">
          <rect class="card-base" width="840" height="510" fill="var(--card-base)"/>
          <path class="card-band" d="M430,0 C640,70 720,250 700,510 L840,510 L840,0 Z" fill="var(--card-band)"/>
          <path class="card-band-light" d="M600,0 C760,90 820,260 790,510 L840,510 L840,0 Z" fill="var(--card-band-light)"/>
        </g>
        <polygon points="48,0 792,0 840,48 840,462 792,510 48,510 0,462 0,48"
                 fill="none" stroke="var(--card-edge)" stroke-width="2"/>
      </svg>

      <div class="brand">
        <span class="brand-dot" aria-hidden="true"></span>
        <span class="brand-name">Brellin Works</span>
      </div>
    </section>
  </main>
</body>
</html>
```